Corporate Travel Technology Company needs new Business Card design

We need a new business card design to reflect our re-branded company. Our company is called tolvEn (pronounced tolvenn) and we provide Business Intelligence and Smarter Journeys For Teams solutions for the corporate travel industry. Our multinational customers use our solutions to manage large travel budgets and frequent travellers, as well as to save money and reduce risk. We'd like to see designs that use the blue and green palette as well as our corporate logo (attached below). The design should communicate innovation, insight, forward thinking, contemporary, trusted.

Target Market(s)

Large multinational corporates and Travel Agencies.

Industry/Entity Type

Business

Contact Information for Business Card

Rosalind Mercer
Chief Executive
tolvEn
Phone number - +61 (0)2 8134 2907
Email address - rosalind.mercer@tolven-example.com
Mobile number - +61 (0)438 516 702
www.tolven-example.com

Font styles to use
Other font styles liked:
• Please use font as close to corporate logo as possible

Colors
0255a3
0393ce
00a990
33b8a4
33a6d7
3176b5

Requirements
Must have
• Please include the words;
• Smarter Journeys For Teams
• Clear Data For Every Corporate Trip
• Use corporate logo - although icon can be stylised if needed

```html
<!DOCTYPE html>
<html lang="en">
<head>
<meta charset="utf-8">
<title>tolvEn Business Card</title>
<link href="https://fonts.googleapis.com/css2?family=Quicksand:wght@300;400;500;700&display=swap" rel="stylesheet">
<style>
  :root {
    --page: #e9ecee;
    --card-white: #ffffff;
    --slate-light: #66787a;
    --slate-dark: #2c393c;
    --slate-text: #3f4b4e;
    --brand-blue: #33a6d7;
    --brand-blue-deep: #0393ce;
    --muted-grey: #8a9597;
    --on-dark: #f2f6f7;
  }
  * { box-sizing: border-box; margin: 0; padding: 0; }
  html, body {
    width: 1200px;
    height: 913px;
    overflow: hidden;
  }
  body {
    position: relative;
    background: var(--page);
    font-family: "Quicksand", sans-serif;
  }
  .card {
    position: absolute;
    width: 525px;
    height: 300px;
    border-radius: 4px;
    overflow: hidden;
    box-shadow: 0 10px 28px rgba(30, 40, 45, 0.22);
  }
  .card-front { left: 70px; top: 110px; background: var(--card-white); }
  .card-back  { left: 605px; top: 500px; }
  .card-art {
    position: absolute;
    inset: 0;
    width: 100%;
    height: 100%;
  }

  /* Front */
  .holder {
    position: absolute;
    right: 30px;
    top: 28px;
    text-align: right;
  }
  .holder-name {
    font-weight: 700;
    font-size: 19px;
    letter-spacing: 0.5px;
    color: var(--brand-blue);
  }
  .holder-title {
    font-weight: 400;
    font-size: 12px;
    color: var(--muted-grey);
    margin-top: 2px;
  }
  .wordmark {
    position: absolute;
    left: 30px;
    top: 118px;
    display: flex;
    align-items: center;
    gap: 10px;
  }
  .wordmark-dot {
    width: 22px;
    height: 22px;
    border-radius: 50%;
    background: var(--brand-blue);
  }
  .wordmark-name {
    font-weight: 500;
    font-size: 54px;
    line-height: 1;
    color: var(--slate-text);
  }
  .contact-list {
    position: absolute;
    right: 24px;
    top: 128px;
    list-style: none;
    text-align: right;
  }
  .contact-item {
    display: flex;
    justify-content: flex-end;
    align-items: center;
    gap: 7px;
    font-weight: 400;
    font-size: 11.5px;
    line-height: 19px;
    color: var(--on-dark);
  }
  .contact-icon {
    width: 9px;
    height: 9px;
    flex: none;
  }

  /* Back */
  .back-mark {
    position: absolute;
    left: 0;
    right: 0;
    top: 92px;
    display: flex;
    justify-content: center;
    align-items: center;
    gap: 14px;
  }
  .back-mark-dot {
    width: 30px;
    height: 30px;
    border-radius: 50%;
    background: var(--brand-blue);
  }
  .back-mark-name {
    font-weight: 500;
    font-size: 58px;
    line-height: 1;
    color: var(--brand-blue);
  }
  .tagline {
    position: absolute;
    left: 0;
    right: 0;
    top: 190px;
    text-align: center;
    font-weight: 700;
    font-size: 14px;
    line-height: 20px;
    color: var(--on-dark);
  }
</style>
</head>
<body>

  <section class="card card-front" aria-label="Business card front">
    <svg class="card-art" viewBox="0 0 525 300" aria-hidden="true">
      <defs>
        <linearGradient id="slateFront" x1="0" y1="0" x2="0.3" y2="1">
          <stop offset="0" stop-color="var(--slate-light)"/>
          <stop offset="1" stop-color="var(--slate-dark)"/>
        </linearGradient>
      </defs>
      <path d="M95 300 C215 292 250 130 370 104 C430 92 485 88 525 86 L525 300 Z" fill="url(#slateFront)"/>
      <path d="M80 300 C205 288 240 118 362 93 C425 80 485 76 525 74" fill="none" stroke="var(--brand-blue)" stroke-width="5"/>
    </svg>

    <div class="holder">
      <p class="holder-name">ROSALIND MERCER</p>
      <p class="holder-title">Chief Executive</p>
    </div>

    <div class="wordmark">
      <span class="wordmark-dot"></span>
      <span class="wordmark-name">tolvEn</span>
    </div>

    <ul class="contact-list">
      <li class="contact-item">+61 (0)438 516 702
        <svg class="contact-icon" viewBox="0 0 10 10"><rect x="2.5" y="0.5" width="5" height="9" rx="1" fill="var(--brand-blue)"/></svg>
      </li>
      <li class="contact-item">+61 (0)2 8134 2907
        <svg class="contact-icon" viewBox="0 0 10 10"><path d="M1 2 C1 6 4 9 8 9 L9 7 L7 6 L6 7 C4.5 6.5 3.5 5.5 3 4 L4 3 L3 1 Z" fill="var(--brand-blue)"/></svg>
      </li>
      <li class="contact-item">www.tolven-example.com
        <svg class="contact-icon" viewBox="0 0 10 10"><circle cx="5" cy="5" r="4.5" fill="var(--brand-blue)"/></svg>
      </li>
      <li class="contact-item">rosalind.mercer@tolven-example.com
        <svg class="contact-icon" viewBox="0 0 10 10"><rect x="0.5" y="2" width="9" height="6.5" rx="1" fill="var(--brand-blue)"/><path d="M1 2.5 L5 5.5 L9 2.5" fill="none" stroke="var(--slate-dark)" stroke-width="0.8"/></svg>
      </li>
    </ul>
  </section>

  <section class="card card-back" aria-label="Business card back">
    <svg class="card-art" viewBox="0 0 525 300" aria-hidden="true">
      <defs>
        <linearGradient id="slateBack" x1="0" y1="0" x2="0.4" y2="1">
          <stop offset="0" stop-color="var(--slate-light)"/>
          <stop offset="1" stop-color="var(--slate-dark)"/>
        </linearGradient>
      </defs>
      <rect width="525" height="300" fill="url(#slateBack)"/>
      <ellipse cx="230" cy="250" rx="240" ry="150" fill="#ffffff" opacity="0.05"/>
      <ellipse cx="470" cy="60" rx="170" ry="190" fill="#ffffff" opacity="0.06"/>
    </svg>

    <div class="back-mark">
      <span class="back-mark-dot"></span>
      <span class="back-mark-name">tolvEn</span>
    </div>

    <p class="tagline">Smarter Journeys For Teams<br>Clear Data For Every Corporate Trip</p>
  </section>

</body>
</html>
```